Home Remodeling company needs a business card design

we need a business card design for home remodeling company in hamilton county, indiana USA. we offers a wide range of construction services including whole house renovations, Design and Build Basements and Kitchen and Bathroom Remodeling . we would like to see designs for both site of business card that use the same color of the company logo and also including all information below :
1- Karim Feltous CEO / General Contractor
2- all company contacts Telephone numbers ( 1-888-DULOM-47 ) ( 317-555-0193) email address ( info@dulomhome.com) website ( www.dulomhome.com ) and social media logos (Facebook- twitter- google plus )
3- company logo
4- licensed . insured . bonded

```html
<!DOCTYPE html>
<html lang="en">
<head>
<meta charset="utf-8">
<title>Dulom Home Remodeling – Business Card</title>
<link rel="stylesheet" href="https://fonts.googleapis.com/css2?family=Arimo:wght@400;700&display=swap">
<style>
  :root {
    --page-bg: #e9e6e2;
    --brand-red: #b82d38;
    --brand-red-deep: #a3232e;
    --charcoal: #3b3b3d;
    --charcoal-text: #404042;
    --paper: #ffffff;
    --soft-white: #f2f2f2;
    --divider: #bdbdbd;
  }
  * { box-sizing: border-box; margin: 0; padding: 0; }
  html, body {
    width: 1200px; height: 902px; overflow: hidden;
    background: var(--page-bg);
    font-family: "Arimo", Arial, sans-serif;
  }
  .sheet {
    width: 1200px; height: 902px;
    display: flex; flex-direction: column;
    align-items: center; justify-content: center; gap: 40px;
  }
  .card {
    position: relative;
    width: 700px; height: 400px;
    overflow: hidden;
    box-shadow: 0 10px 28px rgba(0,0,0,.18);
  }

  /* Back side */
  .card--back { background: var(--brand-red); display: flex; align-items: center; justify-content: center; }
  .card--back .wordmark { color: var(--paper); }
  .card--back .wordmark__square { background: var(--paper); }

  /* Wordmark */
  .wordmark { display: flex; align-items: center; gap: 18px; }
  .wordmark__square { width: 22px; height: 22px; }
  .wordmark__name { font-weight: 700; font-size: 110px; letter-spacing: 4px; line-height: 1; }

  /* Front side */
  .card--front { background: var(--paper); }
  .card__wave { position: absolute; inset: 0; width: 100%; height: 100%; }
  .card--front .wordmark {
    position: absolute; left: 150px; top: 58px; color: var(--charcoal-text);
  }
  .card--front .wordmark__square { background: var(--brand-red); }
  .card--front .wordmark__name { font-size: 84px; }

  .contact-list {
    position: absolute; left: 438px; top: 162px;
    padding-left: 22px;
    border-left: 1.5px solid var(--divider);
    list-style: none;
  }
  .contact-list__item {
    display: flex; align-items: center; gap: 14px;
    height: 32px;
    color: var(--soft-white); font-size: 18px;
  }
  .contact-list__icon {
    width: 20px; height: 20px; flex: none;
    background: var(--soft-white); border-radius: 3px;
    display: flex; align-items: center; justify-content: center;
  }
  .contact-list__icon svg { width: 14px; height: 14px; }

  .holder { position: absolute; left: 40px; bottom: 36px; color: var(--soft-white); }
  .holder__name { font-size: 38px; line-height: 1.1; }
  .holder__title { font-size: 24px; line-height: 1.2; }
</style>
</head>
<body>
<main class="sheet">

  <section class="card card--front" aria-label="Business card front">
    <svg class="card__wave" viewBox="0 0 700 400" preserveAspectRatio="none" aria-hidden="true">
      <path d="M0 252 C 200 282, 370 238, 460 150 C 530 82, 620 58, 700 55 L700 400 L0 400 Z" fill="var(--brand-red)"/>
      <path d="M0 268 C 200 298, 380 256, 470 168 C 540 100, 620 78, 700 74 L700 400 L0 400 Z" fill="var(--charcoal)"/>
    </svg>

    <div class="wordmark">
      <span class="wordmark__square"></span>
      <span class="wordmark__name">DULOM</span>
    </div>

    <ul class="contact-list">
      <li class="contact-list__item">
        <span class="contact-list__icon">
          <svg viewBox="0 0 14 14"><path d="M2 4 Q7 1 12 4 L11 6 L9 5.5 L9 4.5 Q7 4 5 4.5 L5 5.5 L3 6 Z M3 8 H11 V12 H3 Z" fill="var(--charcoal)"/></svg>
        </span>1-888-DULOM-47
      </li>
      <li class="contact-list__item">
        <span class="contact-list__icon">
          <svg viewBox="0 0 14 14"><rect x="4" y="1" width="6" height="12" rx="1" fill="var(--charcoal)"/><rect x="5" y="2.5" width="4" height="7" fill="var(--soft-white)"/></svg>
        </span>317-555-0193
      </li>
      <li class="contact-list__item">
        <span class="contact-list__icon">
          <svg viewBox="0 0 14 14"><rect x="1.5" y="3" width="11" height="8" fill="var(--charcoal)"/><path d="M1.5 3 L7 8 L12.5 3" stroke="var(--soft-white)" stroke-width="1" fill="none"/></svg>
        </span>info@dulomhome.com
      </li>
      <li class="contact-list__item">
        <span class="contact-list__icon">
          <svg viewBox="0 0 14 14"><circle cx="7" cy="7" r="5.5" fill="none" stroke="var(--charcoal)" stroke-width="1.4"/><ellipse cx="7" cy="7" rx="2.3" ry="5.5" fill="none" stroke="var(--charcoal)" stroke-width="1"/><path d="M1.5 7 H12.5" stroke="var(--charcoal)" stroke-width="1"/></svg>
        </span>www.dulomhome.com
      </li>
    </ul>

    <div class="holder">
      <p class="holder__name">Karim Feltous</p>
      <p class="holder__title">CEO / General Contractor</p>
    </div>
  </section>

  <section class="card card--back" aria-label="Business card back">
    <div class="wordmark">
      <span class="wordmark__square"></span>
      <span class="wordmark__name">DULOM</span>
    </div>
  </section>

</main>
</body>
</html>
```